Managed IT services business card design

We haven't needed a business card since the founding of the business in 2005. All our clients have been coming through word of mouth. And lately more and more existing clients are requesting for our business cards to pass on to their contacts in recommending us.
So we needing a business card design. We use various innovative solutions and methodologies to provide IT services to small businesses in managing their IT systems. Our role is the same as an in-house, full-time IT Manager for our clients, but outsourced. So we take care of all our clients' IT needs, just as an IT Manager would be expected to perform.
We have a holding website, which we're happy to leave for now. If we can use the same logo would be great - www.lumadesk.com.au
Preferred colours are shades of are white, grey and black.
We pride our business with the following traits: proactive, good service, prompt response, trustworthy.
Target Market(s)
Small businesses of any industry
Industry/Entity Type
Business

```html
<!DOCTYPE html>
<html lang="en">
<head>
<meta charset="utf-8">
<title>Lumadesk business card</title>
<link rel="stylesheet" href="https://fonts.googleapis.com/css2?family=Open+Sans:wght@400;700&display=swap">
<style>
  :root {
    --page-bg: #e4e6ea;
    --card-light: #f7f7f7;
    --card-mid: #e2e2e2;
    --ink: #2e2e2e;
    --panel-dark: #3a3a3a;
    --swoosh-grey: #b4b4b6;
    --swoosh-light: #d3d3d5;
    --on-dark: #ffffff;
  }
  * { box-sizing: border-box; margin: 0; padding: 0; }
  html, body {
    width: 1200px; height: 866px; overflow: hidden;
    background: var(--page-bg);
    font-family: "Open Sans", Arial, sans-serif;
  }
  .canvas { position: relative; width: 1200px; height: 866px; }
  .card {
    position: absolute; top: 273px;
    width: 560px; height: 320px;
    background: radial-gradient(ellipse at 50% 50%, var(--card-light) 0%, var(--card-mid) 100%);
    box-shadow: 0 6px 18px rgba(0,0,0,0.18);
    overflow: hidden;
  }
  .card--front { left: 20px; }
  .card--back { left: 620px; }
  .card__art { position: absolute; inset: 0; width: 100%; height: 100%; }
  .brand {
    position: absolute; display: flex; align-items: center; gap: 14px;
    font-weight: 400; color: var(--ink); letter-spacing: 0.28em;
  }
  .brand__dot { width: 12px; height: 12px; border-radius: 50%; background: var(--ink); }
  .card--front .brand { left: 50%; top: 50%; transform: translate(-50%, -50%); font-size: 40px; }
  .card--back .brand { left: 34px; top: 96px; font-size: 36px; }
  .holder { position: absolute; left: 40px; top: 198px; color: var(--ink); line-height: 1.25; }
  .holder__name { font-weight: 700; font-size: 17px; }
  .holder__role { font-weight: 400; font-size: 16px; }
  .contact {
    position: absolute; right: 22px; top: 128px;
    color: var(--on-dark); text-align: right;
    font-size: 11.5px; line-height: 1.55;
  }
  .contact__line { display: flex; justify-content: flex-end; align-items: center; gap: 5px; }
  .contact__icon { width: 10px; height: 10px; fill: var(--on-dark); }
</style>
</head>
<body>
<main class="canvas">
  <section class="card card--front" aria-label="Card front">
    <div class="brand"><span class="brand__name">lumadesk</span><span class="brand__dot"></span></div>
  </section>

  <section class="card card--back" aria-label="Card back">
    <svg class="card__art" viewBox="0 0 560 320" preserveAspectRatio="none" aria-hidden="true">
      <path fill="var(--swoosh-light)" d="M430 0 L452 0 C420 40 420 120 360 190 C300 255 170 268 0 270 L0 262 C160 258 290 240 345 180 C400 118 400 40 430 0 Z"/>
      <path fill="var(--swoosh-grey)" d="M446 0 L470 0 C440 30 440 120 380 195 C320 265 170 285 0 288 L0 274 C170 272 305 255 362 192 C420 128 418 36 446 0 Z"/>
      <path fill="var(--panel-dark)" d="M472 0 L560 0 L560 320 L0 320 L0 292 C170 290 320 272 386 200 C446 130 446 34 472 0 Z"/>
      <path fill="var(--swoosh-grey)" d="M120 262 C230 258 320 240 370 200 C330 250 250 268 120 262 Z"/>
    </svg>
    <div class="brand"><span class="brand__name">lumadesk</span><span class="brand__dot"></span></div>
    <div class="holder">
      <p class="holder__name">Dana Holloway</p>
      <p class="holder__role">Consultant</p>
    </div>
    <address class="contact" style="font-style:normal">
      <p class="contact__line">4/18 Harbour Street</p>
      <p class="contact__line">Sydney NSW</p>
      <p class="contact__line">012 345 6789
        <svg class="contact__icon" viewBox="0 0 10 10"><path d="M2 0.5 L3.6 2.6 L2.8 3.6 C3.4 5 5 6.6 6.4 7.2 L7.4 6.4 L9.5 8 L8.6 9.5 C4.5 9.4 0.6 5.5 0.5 1.4 Z"/></svg></p>
      <p class="contact__line">012 345 6789
        <svg class="contact__icon" viewBox="0 0 10 10"><rect x="2" y="0.5" width="6" height="3"/><rect x="0.5" y="4" width="9" height="5.5"/></svg></p>
      <p class="contact__line">urname@email.com
        <svg class="contact__icon" viewBox="0 0 10 10"><rect x="0.5" y="2" width="9" height="6.5"/><path d="M0.5 2 L5 5.5 L9.5 2" stroke="#3a3a3a" stroke-width="1" fill="none"/></svg></p>
      <p class="contact__line">www.yourwebsitename.com</p>
    </address>
  </section>
</main>
</body>
</html>
```